Dovecote Realty

Business cards for 4 people

They need to say for all
87 Tarrow Quay, Boston MA 02114

Each person will have their own personal information
We would like gold embossing for the name of the company
Marla is the blonde sitting in the chair smiling her information should be on the back of the card with her name and information
Should say for slogan classic pattern, elevated experience
grace@dovecoteprops.com
(413) 555-0182

Odette is the brunette with wavy hair in the tan suit odette@dovecoteprops.com
(617) 555-0137

faith@dovecoteprops.com
(413) 555-0164
standing next to the chair

hope@dovecoteprops.com
(413) 555-0199
close up headshot

```html
<!DOCTYPE html>
<html lang="en">
<head>
<meta charset="utf-8">
<title>Dovecote Realty – Business Cards</title>
<link href="https://fonts.googleapis.com/css2?family=Open+Sans:wght@400;600;700&display=swap" rel="stylesheet">
<style>
  :root {
    --page: #2a2a2e;
    --card: #222226;
    --gold: #e8b458;
    --emboss: #141416;
    --emboss-edge: #34343a;
    --text-light: #f4f1ea;
    --portrait-light: #9a6f48;
    --portrait-dark: #3b2c22;
  }
  * { box-sizing: border-box; margin: 0; padding: 0; }
  html, body {
    width: 1200px; height: 780px; overflow: hidden;
    background: var(--page);
    font-family: "Open Sans", Arial, sans-serif;
  }
  .sheet {
    width: 1200px; height: 780px;
    display: flex; align-items: center; justify-content: center; gap: 40px;
  }
  .card {
    position: relative;
    width: 560px; height: 320px;
    background: var(--card);
    border-left: 2px solid var(--gold);
    border-bottom: 2px solid var(--gold);
    overflow: hidden;
  }

  /* Front */
  .card-front { display: flex; align-items: center; justify-content: center; }
  .front-mark { display: flex; align-items: center; gap: 22px; }
  .front-mark .mark-circle {
    width: 110px; height: 110px; border-radius: 50%;
    border: 4px solid var(--emboss);
    box-shadow: 0 1px 0 var(--emboss-edge);
  }
  .front-mark .mark-name {
    color: var(--emboss);
    font-weight: 600;
    font-size: 40px;
    line-height: 1.1;
    letter-spacing: 2px;
    text-transform: uppercase;
    text-shadow: 0 1px 0 var(--emboss-edge);
  }
  .front-mark .mark-name span { display: block; font-size: 18px; letter-spacing: 14px; }

  /* Back */
  .gold-tab {
    position: absolute; top: 0; right: 0;
    width: 18px; height: 56px; background: var(--gold);
  }
  .agent { position: absolute; top: 26px; right: 30px; text-align: right; }
  .agent-name { color: var(--gold); font-weight: 700; font-size: 30px; line-height: 1.1; }
  .agent-title { color: var(--text-light); font-size: 12px; font-weight: 600; margin-top: 2px; }
  .portrait {
    position: absolute; right: 0; bottom: 0;
    width: 230px; height: 220px;
    background: radial-gradient(ellipse at 50% 35%, var(--portrait-light), var(--portrait-dark) 75%, var(--card) 100%);
  }
  .back-mark {
    position: absolute; left: 36px; top: 96px;
    display: flex; align-items: center; gap: 14px;
  }
  .back-mark .mark-circle {
    width: 62px; height: 62px; border-radius: 50%;
    border: 3px solid var(--gold);
  }
  .back-mark .mark-name {
    color: var(--gold); font-weight: 600; font-size: 24px;
    line-height: 1.1; letter-spacing: 1px; text-transform: uppercase;
  }
  .back-mark .mark-name span { display: block; font-size: 11px; letter-spacing: 9px; }
  .contact {
    position: absolute; left: 36px; bottom: 26px;
    color: var(--text-light); font-size: 14px; line-height: 1.45;
    list-style: none;
  }
  .contact .address { margin-bottom: 8px; }
  .contact li { display: flex; align-items: center; gap: 8px; }
  .contact svg { width: 13px; height: 13px; flex: none; }
</style>
</head>
<body>
<main class="sheet">
  <section class="card card-front" aria-label="Card front">
    <div class="front-mark">
      <div class="mark-circle"></div>
      <div class="mark-name">Dovecote<span>Realty</span></div>
    </div>
  </section>

  <section class="card card-back" aria-label="Card back">
    <div class="gold-tab"></div>
    <div class="agent">
      <h1 class="agent-name">Odette Marchand</h1>
      <p class="agent-title">Real Estate Advisor and Sales Manager</p>
    </div>
    <div class="portrait" role="img" aria-label="Portrait photo of Odette, brunette with wavy hair in a tan suit"></div>

    <div class="back-mark">
      <div class="mark-circle"></div>
      <div class="mark-name">Dovecote<span>Realty</span></div>
    </div>

    <ul class="contact">
      <li class="address">87 Tarrow Quay,<br>Boston MA 02114</li>
      <li>
        <svg viewBox="0 0 16 16" aria-hidden="true"><path fill="var(--gold)" d="M3.6 1.5l2.3 2.6-1.3 1.6c.9 2 2.6 3.7 4.6 4.6l1.6-1.3 2.6 2.3-1.2 2.2C7.2 13.8 2.2 8.8 1.5 3.8z"/></svg>
        (617) 555-0137
      </li>
      <li>
        <svg viewBox="0 0 16 16" aria-hidden="true"><g fill="none" stroke="var(--gold)" stroke-width="1.4"><circle cx="8" cy="8" r="6.5"/><ellipse cx="8" cy="8" rx="2.8" ry="6.5"/><path d="M1.5 8h13"/></g></svg>
        www.dovecoteprops.com
      </li>
      <li>
        <svg viewBox="0 0 16 16" aria-hidden="true"><g fill="none" stroke="var(--gold)" stroke-width="1.4"><rect x="1.5" y="3.5" width="13" height="9"/><path d="M1.5 3.5L8 9l6.5-5.5"/></g></svg>
        odette@dovecoteprops.com
      </li>
    </ul>
  </section>
</main>
</body>
</html>
```